Newspaper Ad for a new concept medical clinic

I have uploaded a sample ad. I would prefer the black areas to be the same color blue as the word CuraFinch in the attached file. Instead of a doctor I would like a concerned or worried looking middle age couple 40s/50s as a picture.

702 number will need to change to a toll free number that I will have available next week.
Change web address to www.valbrookmd.example

I would like the bullet points to be changed as follows:
- Affordable Access To Board Certified Physician
- Committment To Excellence In Primary Medical Care
- $10 Office Visits / No Charge Telemedicine Visits
- Adults - $69/month & Teens to Age 26 - $19/month
- Lowest Rates For Lab Tests, Imaging, and Medications

Keep the As Seen In section unchanged
Updates

Ii would like full color. Also I will call the local newspaper today and find the exact dimensenions and update everyone. Thank you all for interest and input.

3 columns(4.9" wide) by 5.25" tall

Please review your submission for readability at the size proposed. The actual ad size is 4.9" wide by 5.25 in tall. There are many wonderful submissions. I am truly impressed.

Full Color

Make sure the copy is readable at this ad size. My last request is for you to add the following term somewhere: Limited Enrollment Call Now

Industry/Entity Type

Medical

```html
<!DOCTYPE html>
<html lang="en">
<head>
<meta charset="utf-8">
<title>CuraFinch Direct Primary Care – Newspaper Ad</title>
<link href="https://fonts.googleapis.com/css2?family=Montserrat:wght@300;400;500;600;700&display=swap" rel="stylesheet">
<style>
  :root {
    --blue-deep: #1a5fa8;
    --blue-mid: #2a7cc6;
    --blue-light: #4aa0e0;
    --brand-blue: #1d78c1;
    --orange: #f18a21;
    --orange-dark: #d9741a;
    --green: #8cc63f;
    --green-dark: #6fae2a;
    --white: #ffffff;
    --ink: #1e3550;
  }
  * { box-sizing: border-box; margin: 0; padding: 0; }
  html, body { width: 935px; height: 1200px; overflow: hidden; background: var(--white); }
  .ad {
    position: relative;
    width: 935px;
    height: 1200px;
    overflow: hidden;
    font-family: "Montserrat", Arial, sans-serif;
    color: var(--white);
    background: radial-gradient(ellipse at 50% 70%, var(--blue-light) 0%, var(--blue-mid) 45%, var(--blue-deep) 100%);
  }
  .headline {
    position: absolute;
    top: 18px;
    left: 0;
    width: 100%;
    text-align: center;
    line-height: 1.02;
    text-shadow: 0 2px 6px rgba(0, 40, 90, 0.35);
  }
  .headline .line { display: block; font-size: 84px; font-weight: 300; letter-spacing: 0.5px; }
  .headline strong { font-weight: 700; }
  .photo-band { position: absolute; top: 205px; left: 0; width: 935px; height: 480px; }
  .photo {
    position: absolute;
    top: 22px;
    left: 0;
    width: 935px;
    height: 440px;
    background:
      linear-gradient(180deg, #9cc3dc 0%, #6a9fc2 30%, #c7b49a 62%, #a88c70 100%);
  }
  .photo-band svg { position: absolute; left: 0; width: 935px; }
  .photo-band .edge-top { top: 0; height: 60px; }
  .photo-band .edge-bottom { bottom: 0; height: 60px; }
  .benefits {
    position: absolute;
    top: 690px;
    left: 0;
    width: 100%;
    list-style: none;
    text-align: center;
    font-size: 25.5px;
    font-weight: 400;
    line-height: 35px;
  }
  .cta {
    position: absolute;
    top: 878px;
    left: 144px;
    width: 640px;
    height: 62px;
    background: linear-gradient(180deg, var(--green) 0%, var(--green-dark) 100%);
    box-shadow: 0 3px 6px rgba(0, 30, 70, 0.35);
    text-align: center;
    font-size: 35px;
    font-weight: 700;
    line-height: 62px;
    color: var(--white);
    text-shadow: 0 1px 3px rgba(0, 0, 0, 0.3);
  }
  .brand-card {
    position: absolute;
    top: 963px;
    left: 220px;
    width: 518px;
    height: 175px;
    background: var(--white);
    border-radius: 22px 22px 0 0;
    text-align: center;
    padding-top: 34px;
  }
  .brand-name {
    display: inline-flex;
    align-items: center;
    gap: 14px;
    font-size: 62px;
    font-weight: 500;
    color: var(--brand-blue);
    line-height: 1;
  }
  .brand-name .dot { width: 34px; height: 34px; border-radius: 50%; background: var(--orange); }
  .brand-tagline { margin-top: 12px; font-size: 28px; font-weight: 600; color: var(--orange); }
  .footer {
    position: absolute;
    bottom: 0;
    left: 0;
    width: 935px;
    height: 68px;
    background: var(--orange);
    display: flex;
    align-items: center;
    justify-content: center;
    font-size: 31px;
    font-weight: 400;
    white-space: nowrap;
  }
  .footer b { font-weight: 700; }
</style>
</head>
<body>
<main class="ad">
  <h1 class="headline">
    <span class="line">Can’t Afford</span>
    <span class="line"><strong>Health</strong> Benefits?</span>
  </h1>

  <div class="photo-band">
    <div class="photo" role="img" aria-label="Photo of a concerned middle-aged couple sitting together by the waterfront"></div>
    <svg class="edge-top" viewBox="0 0 935 60" preserveAspectRatio="none" aria-hidden="true">
      <path d="M0 36 Q467 -8 935 36 L935 0 L0 0 Z" fill="var(--blue-deep)"/>
      <path d="M0 36 Q467 -8 935 36" fill="none" stroke="var(--orange)" stroke-width="5"/>
    </svg>
    <svg class="edge-bottom" viewBox="0 0 935 60" preserveAspectRatio="none" aria-hidden="true">
      <path d="M0 30 Q467 -6 935 30 L935 60 L0 60 Z" fill="var(--blue-mid)"/>
      <path d="M0 30 Q467 -6 935 30" fill="none" stroke="var(--orange)" stroke-width="5"/>
    </svg>
  </div>

  <ul class="benefits">
    <li>- Affordable Access To Board Certified Physician</li>
    <li>- Committment To Excellence In Primary Medical Care</li>
    <li>- $10 Office Visits / No Charge Telemedicine Visits</li>
    <li>- Adults - $69/month &amp; Teens to Age 26 - $19/month</li>
    <li>- Lowest Rates For Lab Tests, Imaging, and Medications</li>
  </ul>

  <div class="cta">Limited Enrollment Call Now</div>

  <div class="brand-card">
    <div class="brand-name">CuraFinch<span class="dot" aria-hidden="true"></span></div>
    <div class="brand-tagline">Direct Primary Care</div>
  </div>

  <footer class="footer">
    <span><b>Call to sign up</b>: 702-555-0147 / <b>www.valbrookmd.example</b></span>
  </footer>
</main>
</body>
</html>
```